Premium Packaging Design for a Line of Four Beeswax Candle Scents

Need to design a beeswax quality candle design for ceramic and tube packaging. The ceramic jar size is 11oz (311g) and should be on the label with reference to hand poured or hand crafted.
4 scents that match our branding for our incense. Scents are : 1) Honey Lavender 2) Coconut Honey 3) Velvet Dusk 4) Midnight Harbor. Each tube must have elements of each of its scents i.e midnight harbor should make reference to coffee. Die Line for the candle packaging sizing is attached in files. Design is for the tube packaging only. Must include warning label on the bottom with barcode (dummy barcode can be used for design phase). Logo and other design elements can be taken from .ai incense box. Elements of bees such as wax comb or hexagonal shapes should be used.
Bottom Warning Label (text):
1) Warning Triangle should be in Yellow
2) Icons (attached should be used)
3) Wording:
Always burn within sight and never in drafty conditions
Keep away from things that catch fire
Keep away from children and pets
4) Burn Instructions
Trim wick to 1/4" each time candle is lit. Keep wax pool free of debris including matches and wick trimmings. Only burn candle on level fire resistant surface. Do not burn candle for more than 4 hours at a time.

Target Market(s)

USA market. Must have MADE IN USA on packaging

Industry/Entity Type

Health and Beauty

Font styles to use
Decorative
Script

Requirements
Must have
• Gold stamping
Nice to have
• Follow branded guidelines as per our incense box
Should not have
• cheap and generic stock images

```html
<!DOCTYPE html>
<html lang="en">
<head>
<meta charset="utf-8">
<title>Honey Lavender Candle Tube – Dieline Layout</title>
<link rel="stylesheet" href="https://fonts.googleapis.com/css2?family=Cinzel:wght@400;600&family=Crimson+Text:ital,wght@0,400;0,600;0,700;1,400&family=Open+Sans:wght@400;700;800&family=Tinos&display=swap">
<style>
  :root {
    --paper: #ffffff;
    --dim-red: #e0101a;
    --guide-red: #e0101a;
    --hex-black: #120c06;
    --gold: #d9b24c;
    --gold-light: #f4dc8a;
    --gold-deep: #8c6420;
    --lavender-deep: #3b1a63;
    --lavender-mid: #7a4bb0;
    --lavender-light: #a884d6;
    --ink-white: #f5f0ea;
    --warn-yellow: #ffd200;
    --caption: #111111;
  }
  html, body {
    margin: 0;
    padding: 0;
    width: 1200px;
    height: 988px;
    overflow: hidden;
    background: var(--paper);
  }
  .dieline-sheet {
    display: block;
    width: 1200px;
    height: 988px;
  }
  .dim-label {
    font-family: "Tinos", "Times New Roman", serif;
    fill: var(--dim-red);
  }
  .caption {
    font-family: "Open Sans", Arial, sans-serif;
    fill: var(--caption);
  }
  .hex-kicker {
    font-family: "Crimson Text", Georgia, serif;
    font-weight: 700;
    fill: var(--ink-white);
  }
  .hex-title {
    font-family: "Cinzel", Georgia, serif;
    font-weight: 600;
    fill: url(#goldFoil);
  }
  .hex-sub {
    font-family: "Crimson Text", Georgia, serif;
    fill: var(--ink-white);
  }
  .story-copy text {
    font-family: "Crimson Text", Georgia, serif;
    fill: var(--ink-white);
  }
  .brand-name {
    font-family: "Cinzel", Georgia, serif;
    font-weight: 600;
    fill: var(--gold);
  }
  .warn-head {
    font-family: "Open Sans", Arial, sans-serif;
    font-weight: 800;
    fill: #ffffff;
  }
  .warn-copy text {
    font-family: "Open Sans", Arial, sans-serif;
    fill: #ffffff;
  }
  .barcode-label {
    font-family: "Open Sans", Arial, sans-serif;
    fill: #111111;
  }
</style>
</head>
<body>
<svg class="dieline-sheet" viewBox="0 0 1200 988" xmlns="http://www.w3.org/2000/svg">
  <defs>
    <linearGradient id="goldFoil" x1="0" y1="0" x2="0" y2="1">
      <stop offset="0" stop-color="#f7e39a"/>
      <stop offset="0.5" stop-color="#d4a845"/>
      <stop offset="1" stop-color="#8c6420"/>
    </linearGradient>
    <linearGradient id="goldRule" x1="0" y1="0" x2="1" y2="0">
      <stop offset="0" stop-color="#d9b24c" stop-opacity="0"/>
      <stop offset="0.5" stop-color="#f4dc8a"/>
      <stop offset="1" stop-color="#d9b24c" stop-opacity="0"/>
    </linearGradient>
    <linearGradient id="wrapField" x1="0" y1="0" x2="1" y2="0">
      <stop offset="0" stop-color="#5a2f8f"/>
      <stop offset="0.2" stop-color="#8a5ab8"/>
      <stop offset="0.4" stop-color="#b48a6a"/>
      <stop offset="0.55" stop-color="#7b4cb2"/>
      <stop offset="0.75" stop-color="#6a2f8e"/>
      <stop offset="0.9" stop-color="#8a4aa8"/>
      <stop offset="1" stop-color="#5a2f8f"/>
    </linearGradient>
    <radialGradient id="storyPanel" cx="0.5" cy="0.45" r="0.6">
      <stop offset="0" stop-color="#9a4ab8"/>
      <stop offset="1" stop-color="#4a1c6e" stop-opacity="0"/>
    </radialGradient>
    <radialGradient id="lidField" cx="0.5" cy="0.45" r="0.55">
      <stop offset="0" stop-color="#9a78d0"/>
      <stop offset="0.7" stop-color="#6a44a8"/>
      <stop offset="1" stop-color="#1a0f24"/>
    </radialGradient>
    <linearGradient id="ornamentField" x1="0" y1="0" x2="0" y2="1">
      <stop offset="0" stop-color="#b88a34" stop-opacity="0.55"/>
      <stop offset="1" stop-color="#6e4c18" stop-opacity="0.35"/>
    </linearGradient>
  </defs>

  <!-- Dimension annotations -->
  <g class="dimensions">
    <text class="dim-label" x="633" y="24" font-size="31" text-anchor="middle">310.8 mm</text>
    <line x1="142" y1="34" x2="1122" y2="34" stroke="var(--dim-red)" stroke-width="1"/>
    <line x1="142" y1="18" x2="142" y2="50" stroke="var(--dim-red)" stroke-width="1"/>
    <line x1="1122" y1="18" x2="1122" y2="50" stroke="var(--dim-red)" stroke-width="1"/>
    <polygon points="142,34 164,24 164,44" fill="var(--dim-red)"/>
    <polygon points="1122,34 1100,24 1100,44" fill="var(--dim-red)"/>

    <line x1="92" y1="98" x2="126" y2="98" stroke="var(--dim-red)" stroke-width="1"/>
    <line x1="92" y1="212" x2="126" y2="212" stroke="var(--dim-red)" stroke-width="1"/>
    <line x1="92" y1="481" x2="126" y2="481" stroke="var(--dim-red)" stroke-width="1"/>
    <line x1="109" y1="98" x2="109" y2="481" stroke="var(--dim-red)" stroke-width="1"/>
    <polygon points="109,98 99,120 119,120" fill="var(--dim-red)"/>
    <polygon points="109,212 99,190 119,190" fill="var(--dim-red)"/>
    <polygon points="109,212 99,234 119,234" fill="var(--dim-red)"/>
    <polygon points="109,481 99,459 119,459" fill="var(--dim-red)"/>
    <text class="dim-label" font-size="31" text-anchor="middle" transform="translate(89,155) rotate(-90)">36 mm</text>
    <text class="dim-label" font-size="31" text-anchor="middle" transform="translate(89,346) rotate(-90)">85 mm</text>
  </g>

  <!-- Tube wrap label -->
  <g class="tube-wrap">
    <rect x="126" y="55" width="1035" height="471" fill="url(#wrapField)" role="img" aria-label="Lavender sprigs over a honeycomb and golden backdrop"/>
    <rect x="800" y="90" width="280" height="380" fill="url(#storyPanel)"/>

    <g class="bleed-guides" fill="none" stroke="var(--guide-red)" stroke-width="0.8">
      <rect x="133" y="61" width="1022" height="458"/>
      <rect x="142" y="70" width="981" height="439"/>
      <line x1="142" y1="98" x2="1123" y2="98"/>
      <line x1="142" y1="212" x2="1123" y2="212"/>
      <line x1="142" y1="481" x2="1123" y2="481"/>
    </g>

    <g class="wrap-seal">
      <polygon points="341,141 501,141 586,290 501,441 341,441 256,290" fill="var(--hex-black)"/>
      <polygon points="346,150 496,150 576,290 496,432 346,432 266,290" fill="none" stroke="var(--gold)" stroke-width="3"/>
      <text class="hex-kicker" x="417" y="202" font-size="14" text-anchor="middle" textLength="131" lengthAdjust="spacingAndGlyphs">NATURAL BEESWAX</text>
      <rect x="380" y="220" width="76" height="40" fill="url(#ornamentField)" role="img" aria-label="Gold filigree crest ornament"/>
      <rect x="290" y="264" width="260" height="2.5" fill="url(#goldRule)"/>
      <text class="hex-title" x="421" y="302" font-size="31" text-anchor="middle" textLength="272" lengthAdjust="spacingAndGlyphs">HONEY LAVENDER</text>
      <rect x="290" y="309" width="260" height="2.5" fill="url(#goldRule)"/>
      <rect x="380" y="316" width="76" height="46" fill="url(#ornamentField)" role="img" aria-label="Gold filigree crest ornament"/>
      <text class="hex-sub" x="420" y="388" font-size="16" text-anchor="middle" textLength="111" lengthAdjust="spacingAndGlyphs">HAND CRAFTED</text>
      <text class="hex-sub" x="410" y="423" font-size="8" text-anchor="middle">NET WT. 11oz (311G)</text>
    </g>

    <g class="story-copy" font-size="13" text-anchor="middle">
      <text x="929" y="194">Only the highest quality 100%</text>
      <text x="929" y="213">pure American beeswax is</text>
      <text x="929" y="233">sourced by Solenne to create our</text>
      <text x="929" y="252">range of candles, guaranteeing</text>
      <text x="929" y="272">sustainability. Our beeswax</text>
      <text x="929" y="291">candles burn longer and cleaner</text>
      <text x="929" y="311">than traditional candles.</text>
      <text x="929" y="331">releasing a delicate blend of</text>
      <text x="929" y="350">honey-scented fragrance that</text>
      <text x="929" y="370">will transport your senses.</text>
      <text x="929" y="409">PRODUCT OF USA</text>
    </g>
  </g>

  <!-- Front seal -->
  <g class="front-seal">
    <polygon points="149,600 317,600 400,750 317,900 149,900 67,750" fill="var(--hex-black)" stroke="#e8e0ea" stroke-width="1"/>
    <polygon points="154,610 312,610 390,750 312,890 154,890 77,750" fill="none" stroke="var(--gold)" stroke-width="3"/>
    <text class="hex-kicker" x="230" y="661" font-size="14" text-anchor="middle" textLength="132" lengthAdjust="spacingAndGlyphs">NATURAL BEESWAX</text>
    <rect x="195" y="676" width="76" height="44" fill="url(#ornamentField)" role="img" aria-label="Gold filigree crest ornament"/>
    <rect x="100" y="724" width="266" height="2.5" fill="url(#goldRule)"/>
    <text class="hex-title" x="234" y="762" font-size="31" text-anchor="middle" textLength="273" lengthAdjust="spacingAndGlyphs">HONEY LAVENDER</text>
    <rect x="100" y="768" width="266" height="2.5" fill="url(#goldRule)"/>
    <rect x="195" y="776" width="76" height="46" fill="url(#ornamentField)" role="img" aria-label="Gold filigree crest ornament"/>
    <text class="hex-sub" x="233" y="847" font-size="16" text-anchor="middle" textLength="111" lengthAdjust="spacingAndGlyphs">HAND CRAFTED</text>
    <text class="hex-sub" x="230" y="881" font-size="8" text-anchor="middle">NET WT. 11oz (311G)</text>
    <text class="caption" x="220" y="940" font-size="24" text-anchor="middle">Front</text>
  </g>

  <!-- Top lid label -->
  <g class="lid-top">
    <text class="dim-label" x="617" y="578" font-size="26" text-anchor="middle">上</text>
    <circle cx="621" cy="744" r="162" fill="url(#lidField)" role="img" aria-label="Bunch of lavender blossoms on black"/>
    <circle cx="621" cy="744" r="158" fill="none" stroke="var(--guide-red)" stroke-width="0.8"/>
    <rect x="504" y="717" width="232" height="65" fill="var(--hex-black)" stroke="var(--gold)" stroke-width="3"/>
    <text class="brand-name" x="620" y="764" font-size="37" text-anchor="middle" textLength="180" lengthAdjust="spacingAndGlyphs">SOLENNE</text>
    <text class="dim-label" x="618" y="948" font-size="26" text-anchor="middle">D:  99mm</text>
    <text class="caption" x="614" y="978" font-size="24" text-anchor="middle">Top</text>
  </g>

  <!-- Bottom warning label -->
  <g class="lid-bottom">
    <text class="dim-label" x="1040" y="578" font-size="26" text-anchor="middle">下</text>
    <circle cx="1039" cy="744" r="160" fill="var(--hex-black)"/>
    <circle cx="1039" cy="744" r="156" fill="none" stroke="var(--guide-red)" stroke-width="0.8"/>
    <polygon points="1037,597 1068,653 1006,653" fill="var(--warn-yellow)"/>
    <rect x="1034" y="610" width="6" height="28" rx="3" fill="var(--hex-black)"/>
    <circle cx="1037" cy="645" r="3.5" fill="var(--hex-black)"/>
    <text class="warn-head" x="1038" y="686" font-size="30" text-anchor="middle" textLength="162" lengthAdjust="spacingAndGlyphs">WARNING!</text>

    <g class="warn-icons" fill="none" stroke="#ffffff" stroke-width="3">
      <circle cx="977" cy="720" r="24"/>
      <line x1="960" y1="703" x2="994" y2="737"/>
      <circle cx="1036" cy="720" r="24"/>
      <line x1="1019" y1="703" x2="1053" y2="737"/>
      <circle cx="1095" cy="720" r="24"/>
      <line x1="1078" y1="703" x2="1112" y2="737"/>
    </g>

    <g class="warn-copy" font-size="6">
      <text x="918" y="758">Keep away from things that catch fire</text>
      <text x="918" y="767">Keep away from children and pets</text>
      <text x="918" y="776">Always burn within sight and never in drafty conditions</text>
      <text x="918" y="790" font-size="8" font-weight="700">Burn Instructions:</text>
      <text x="918" y="801" textLength="252" lengthAdjust="spacingAndGlyphs">Trim wick to 1/4" each time candle is lit. Keep wax pool free of debris including matches and</text>
      <text x="918" y="810" textLength="242" lengthAdjust="spacingAndGlyphs">wick trimmings. Only burn candle on level fire resistant surface. Do not burn candle for</text>
      <text x="918" y="819">more than 4 hours at a time.</text>
    </g>

    <rect x="988" y="829" width="107" height="42" fill="#ffffff"/>
    <text class="barcode-label" x="1041" y="857" font-size="18" text-anchor="middle">BARCODE</text>

    <text class="dim-label" x="1046" y="936" font-size="26" text-anchor="middle">D:  99mm</text>
    <text class="caption" x="1057" y="978" font-size="24" text-anchor="middle">Bottom</text>
  </g>
</svg>
</body>
</html>
```